Construction business card

I need a new business card, they can connect with my logo, brand.
What we do is residential house , design and build
I like: Navy blue / black
I attached our logo, brand,
and, some idea for business card.

```html
<!DOCTYPE html>
<html lang="en">
<head>
<meta charset="utf-8">
<title>Norwood Building Group – Business Card</title>
<link href="https://fonts.googleapis.com/css2?family=Lato:wght@400;700;900&display=swap" rel="stylesheet">
<style>
  :root {
    --backdrop: #2b2b2d;
    --card: #0a0a0b;
    --blue: #3b82f0;
    --white: #ffffff;
    --text: #f2f2f2;
  }
  * { margin: 0; padding: 0; box-sizing: border-box; }
  html, body { width: 1200px; height: 1200px; overflow: hidden; background: var(--backdrop); }
  body { position: relative; font-family: "Lato", sans-serif; color: var(--text); }

  .card {
    position: absolute;
    left: 272px;
    width: 686px;
    height: 394px;
    background: var(--card);
    border-radius: 28px;
  }
  .card--front { top: 194px; }
  .card--back { top: 618px; }

  .accent-bar { position: absolute; left: 0; top: 106px; width: 8px; height: 46px; background: var(--blue); }

  .person { position: absolute; left: 29px; top: 104px; }
  .person__name { font-size: 27px; font-weight: 400; color: var(--blue); letter-spacing: 0.2px; line-height: 1.1; }
  .person__role { margin-top: 10px; font-size: 18px; line-height: 1; }

  .address { position: absolute; left: 28px; top: 195px; font-size: 19px; line-height: 26px; font-style: normal; }

  .contacts { position: absolute; left: 28px; top: 262px; list-style: none; }
  .contacts li { display: flex; align-items: center; height: 31px; font-size: 19px; }
  .contacts svg { width: 20px; height: 20px; margin-right: 16px; fill: var(--blue); }

  .brand {
    position: absolute;
    display: flex; flex-direction: column; align-items: center;
    font-weight: 900; color: var(--white); text-transform: uppercase; text-align: center;
  }
  .card--front .brand { left: 336px; width: 326px; top: 112px; }
  .card--back .brand { left: 170px; width: 346px; top: 118px; }
  .brand__mark { width: 34px; height: 34px; background: var(--blue); margin-bottom: 14px; }
  .brand__name { font-size: 62px; line-height: 1; letter-spacing: 2px; }
  .brand__sub { font-size: 29px; line-height: 1.2; letter-spacing: 1.5px; margin-top: 6px; }
  .card--back .brand__name { font-size: 66px; }
  .card--back .brand__sub { font-size: 31px; }
</style>
</head>
<body>
  <section class="card card--front">
    <span class="accent-bar"></span>
    <div class="person">
      <h1 class="person__name">DANIEL ARCHER</h1>
      <p class="person__role">Owner</p>
    </div>
    <address class="address">27 Ferncliff Street,<br>Oakvale, Vic 3190</address>
    <ul class="contacts">
      <li>
        <svg viewBox="0 0 24 24" aria-hidden="true"><path d="M6.6 10.8a15.1 15.1 0 0 0 6.6 6.6l2.2-2.2a1 1 0 0 1 1-.25 11.4 11.4 0 0 0 3.6.57 1 1 0 0 1 1 1V20a1 1 0 0 1-1 1A17 17 0 0 1 3 4a1 1 0 0 1 1-1h3.5a1 1 0 0 1 1 1c0 1.25.2 2.45.57 3.57a1 1 0 0 1-.25 1z"/></svg>
        0400 555 218
      </li>
      <li>
        <svg viewBox="0 0 24 24" aria-hidden="true"><path d="M2 5h20v14H2z M2 5l10 8 10-8" /><path d="M2 5h20l-10 8z" fill="#0a0a0b" opacity="0.35"/></svg>
        hello@norwoodbg.com
      </li>
      <li>
        <svg viewBox="0 0 24 24" aria-hidden="true"><path d="M12 2a10 10 0 1 0 0 20 10 10 0 0 0 0-20zm-1 17.9A8 8 0 0 1 4.1 10L9 15v1a2 2 0 0 0 2 2zm6.9-2.5A2 2 0 0 0 16 16h-1v-3a1 1 0 0 0-1-1H8v-2h2a1 1 0 0 0 1-1V7h2a2 2 0 0 0 2-2v-.4a8 8 0 0 1 2.9 12.8z"/></svg>
        www.norwoodbg.com
      </li>
    </ul>
    <div class="brand">
      <span class="brand__mark"></span>
      <span class="brand__name">Norwood</span>
      <span class="brand__sub">Building Group</span>
    </div>
  </section>

  <section class="card card--back">
    <div class="brand">
      <span class="brand__mark"></span>
      <span class="brand__name">Norwood</span>
      <span class="brand__sub">Building Group</span>
    </div>
  </section>
</body>
</html>
```